Stationery Set for Velmora Company

I need to create full stationery design for my company; Business Cards, Envelops, Letter Heads, Calendar.
In the letter head and Envelops... only contact information and website links.
Our company is a Service Management company with different domains of innovative services including Technology Service Management, Education Services, Outsourcing Management, Events Management.
I need a modern and innovative design specially for the business card. I some transparent designs and I like it, but don't limit your innovation to what I mentioned. Sky is limit for your innovation.

Target Market(s)

Middle East & Africa

Industry/Entity Type

Business Management

Colors
34a7d8
0355a3
85acd3
86cae7
cee9f5
cfdeed
e4daeb
f3f1f8
ecf7fb

Requirements
Must have
• Name, Title, Email, Mobile
Nice to have
• We have multiple locations in USA, KSA, EGY, so I need ideas about how to include all contact details maybe QR / Barcode or something else.
• Please see our locations and contact information: www.brightvelmora.example
Should not have
• Too much text

```html
<!DOCTYPE html>
<html lang="en">
<head>
<meta charset="utf-8">
<title>Velmora Company – Business Card</title>
<link href="https://fonts.googleapis.com/css2?family=Fira+Sans+Condensed:wght@400;500;600&display=swap" rel="stylesheet">
<style>
  :root {
    --backdrop: #9b9b9b;
    --card: #f1f1f3;
    --brand-blue: #2f5a9e;
    --name-blue: #3a5fa3;
    --ink: #1d1d1f;
    --on-band: #ffffff;
    --pattern: #d9dde8;
    --rule: #b9c3d6;
  }
  * { margin: 0; padding: 0; box-sizing: border-box; }
  html, body {
    width: 1105px; height: 1200px; overflow: hidden;
    background: var(--backdrop);
    font-family: "Fira Sans Condensed", "Arial Narrow", sans-serif;
  }
  .card {
    position: absolute; left: 182px; width: 746px; height: 427px;
    background: var(--card);
    overflow: hidden;
  }
  .card--front { top: 119px; }
  .card--back { top: 637px; }

  .holder { position: absolute; left: 46px; top: 46px; }
  .holder__name {
    font-size: 31px; font-weight: 500; letter-spacing: 0.5px;
    color: var(--name-blue); line-height: 1;
  }
  .holder__title {
    margin-top: 14px; font-size: 20px; color: var(--ink); line-height: 1;
  }

  .brand {
    position: absolute; display: flex; flex-direction: column; align-items: center;
    color: var(--brand-blue); font-weight: 600;
  }
  .brand__name { font-size: 40px; line-height: 1; letter-spacing: 0.5px; }
  .brand__rule { margin-top: 14px; width: 100%; height: 1px; background: var(--rule); }
  .card--front .brand { left: 423px; top: 68px; width: 280px; }
  .card--back .brand { left: 218px; top: 98px; width: 310px; }

  .band {
    position: absolute; left: 0; top: 225px; width: 100%; height: 171px;
    background: var(--brand-blue); color: var(--on-band);
  }
  .office {
    position: absolute; top: 19px; font-size: 16.5px; line-height: 22px;
  }
  .office__region { font-size: 17px; }
  .office--ksa { left: 35px; }
  .office--usa { left: 254px; }

  .contacts { position: absolute; left: 456px; top: 80px; list-style: none; font-size: 16.5px; }
  .contacts li { display: flex; align-items: center; height: 29px; }
  .contacts svg { width: 18px; height: 18px; margin-right: 8px; flex: none; }

  .bulb-pattern {
    position: absolute; left: 0; top: 240px; width: 100%; height: 187px;
    background: linear-gradient(180deg, var(--card) 0%, var(--pattern) 100%);
  }
</style>
</head>
<body>
  <section class="card card--front" aria-label="Business card front">
    <div class="holder">
      <p class="holder__name">ADAM RAHAL</p>
      <p class="holder__title">CEO/FOUNDER</p>
    </div>
    <div class="brand">
      <span class="brand__name">Velmora Company</span>
      <span class="brand__rule"></span>
    </div>
    <div class="band">
      <address class="office office--ksa">
        <span class="office__region">SAUDI ARABIA:</span><br>
        Riyadh, Al Olaya,<br>
        Nakheel Rd.<br>
        Qamar Buildings<br>
        Block 4C 3rd Floor C12, C14<br>
        Phone : +966 92000 11 80
      </address>
      <address class="office office--usa">
        <span class="office__region">USA:</span><br>
        512 Harbor Point Way<br>
        4th Floor Lakeview City<br>
        CA 94000 US<br>
        Phone:+1.6505550142
      </address>
      <ul class="contacts">
        <li>
          <svg viewBox="0 0 18 18" fill="none" stroke="#fff" stroke-width="1.6"><rect x="5" y="1.5" width="8" height="15" rx="1.5"/><line x1="8" y1="14" x2="10" y2="14"/></svg>
          +1.6505550142
        </li>
        <li>
          <svg viewBox="0 0 18 18" fill="#fff"><rect x="1.5" y="4" width="15" height="10" rx="1"/><path d="M2 4.5 L9 10 L16 4.5" fill="none" stroke="#2f5a9e" stroke-width="1.4"/></svg>
          info@brightvelmora.example
        </li>
        <li>
          <svg viewBox="0 0 18 18" fill="none" stroke="#fff" stroke-width="1.5"><circle cx="9" cy="9" r="7"/><ellipse cx="9" cy="9" rx="3" ry="7"/><line x1="2" y1="9" x2="16" y2="9"/></svg>
          www.brightvelmora.example
        </li>
      </ul>
    </div>
  </section>

  <section class="card card--back" aria-label="Business card back">
    <div class="brand">
      <span class="brand__name">Velmora Company</span>
      <span class="brand__rule"></span>
    </div>
    <div class="bulb-pattern" role="img" aria-label="Faint repeating pattern of outlined light bulbs"></div>
  </section>
</body>
</html>
```